Marwick Jewelers New Website Design

This project is to provide a new design for an existing website. The existing website is marwickjewelers dot com . I have created a overview document that outlines all the details for the project. I do not need the design to be converted into HTML. I have a team for that already so please don't ask. I have a lot of images .. too many to upload here so they are on my dev server located at quillfoxstudio com slash marwick slash assets

Number of Pages Required

1 page

```html
<!DOCTYPE html>
<html lang="en">
<head>
<meta charset="utf-8">
<title>Marwick Jewelers</title>
<link href="https://fonts.googleapis.com/css2?family=Roboto:wght@400;500;700&family=Great+Vibes&display=swap" rel="stylesheet">
<style>
:root{
  --teal:#5fa2b8;
  --ink:#2f2f2f;
  --text:#555;
  --muted:#8a8a8a;
  --line:#e3e3e3;
  --soft:#f5f5f5;
  --footer:#58585a;
  --white:#fff;
}
*{margin:0;padding:0;box-sizing:border-box}
html,body{width:1200px;height:3199px;overflow:hidden}
body{position:relative;background:var(--white);font-family:'Roboto',sans-serif;color:var(--ink)}
.abs{position:absolute}
.script{font-family:'Great Vibes',cursive;font-weight:400}
.script .accent{color:var(--teal)}

/* header */
.call{left:265px;top:18px;display:flex;align-items:center;gap:14px}
.call-icon{width:44px;height:44px;border-radius:50%;background:#eef1f3;display:flex;align-items:center;justify-content:center}
.call small{display:block;font-size:11px;color:var(--muted)}
.call strong{display:block;font-size:15px;font-weight:400;color:var(--ink);margin-top:4px}
.header-rule{top:70px;height:1px;background:var(--line)}
.brand{left:525px;width:150px;top:22px;text-align:center}
.brand-dot{width:12px;height:12px;border-radius:50%;border:1.5px solid var(--teal);margin:0 auto 10px}
.brand-name{font-size:17px;font-weight:400;color:var(--ink);white-space:nowrap;letter-spacing:.3px}
.social-top{left:849px;top:21px;display:flex;gap:6px}
.social-btn{width:40px;height:40px;border-radius:50%;background:var(--teal);display:flex;align-items:center;justify-content:center}
.social-btn.light{background:var(--white);box-shadow:0 2px 8px rgba(0,0,0,.15)}
.nav{left:0;top:97px;width:1200px;height:28px;display:flex;justify-content:center;gap:28px;font-size:13px;color:var(--ink);border-bottom:1px solid var(--line)}
.nav .active{color:var(--teal)}

/* hero */
.hero{left:0;top:125px;width:1200px;height:600px;background:linear-gradient(90deg,#c9cfd1 0%,#aeb7b9 35%,#b9a48a 62%,#8d8273 100%)}
.hero-title{left:80px;width:480px;top:322px;text-align:center;font-size:58px;color:var(--ink)}
.hero-copy{left:90px;width:460px;top:400px;text-align:center;font-size:16px;line-height:26px;color:#333}
.btn{display:flex;align-items:center;justify-content:center;border-radius:24px;font-size:15px;font-weight:500}
.hero-btn{left:248px;top:472px;width:146px;height:47px;background:var(--teal);color:var(--white)}
.dots-pill{left:541px;top:705px;width:116px;height:40px;border-radius:20px;background:var(--white);box-shadow:0 3px 10px rgba(0,0,0,.12);display:flex;align-items:center;justify-content:center;gap:14px}
.dots-pill i{width:5px;height:5px;border-radius:50%;background:#444;display:block}
.dots-pill i.on{width:20px;height:20px;border:1.5px solid var(--teal);background:radial-gradient(circle,#444 2.5px,transparent 3px)}

/* section titles */
.section-title{font-size:50px;color:var(--ink)}
.arrow{width:38px;height:38px;border-radius:50%;display:flex;align-items:center;justify-content:center}
.arrow.light{background:var(--white);box-shadow:0 2px 8px rgba(0,0,0,.15)}
.arrow.dark{background:var(--teal)}

/* categories */
.cat{top:903px;width:308px;height:266px}
.cat-label{left:16px;bottom:17px;width:112px;height:40px;border-radius:20px;background:var(--white);display:flex;align-items:center;justify-content:center;font-size:13px;color:var(--ink)}

/* about */
.about-band{left:0;top:1335px;width:1200px;height:429px;background:var(--teal)}
.about-photo{left:112px;top:1271px;width:428px;height:556px;background:linear-gradient(160deg,#d8c4b0 0%,#c9a98e 45%,#6ea9bd 75%,#bcbab2 100%)}
.about-title{left:599px;top:1370px;font-size:48px;color:var(--white)}
.about-copy{left:599px;top:1448px;width:489px;font-size:14.5px;line-height:25.8px;color:var(--white);text-align:justify}
.about-copy p+p{margin-top:11px}
.about-btn{left:599px;top:1673px;width:138px;height:47px;background:var(--white);color:var(--ink)}

/* featured */
.prod{top:1981px;width:231px}
.prod-img{height:273px;background:var(--white);box-shadow:0 2px 10px rgba(0,0,0,.1);display:flex;align-items:center;justify-content:center}
.prod-img div{width:150px;height:150px;border-radius:50%}
.prod h3{margin-top:22px;text-align:center;font-size:17px;font-weight:500;color:var(--teal)}
.prod p{margin-top:10px;text-align:center;font-size:13px;line-height:21px;color:var(--muted)}

/* testimonials */
.reviews{left:0;top:2426px;width:1200px;height:453px;background:var(--soft)}
.review{top:2560px;width:385px;height:208px;background:var(--white);border-radius:6px;box-shadow:0 3px 12px rgba(0,0,0,.08);padding:22px 22px 0}
.review p{margin-top:14px;font-size:13px;line-height:23px;color:var(--muted);text-align:justify}
.who{display:flex;align-items:center;gap:18px;margin-top:16px}
.avatar{width:54px;height:54px;border-radius:50%;background:linear-gradient(135deg,#b48d6d,#5c4a3c)}
.who strong{display:block;font-size:15px;font-weight:400;color:var(--ink)}
.who small{display:block;font-size:12px;color:var(--muted);margin-top:4px}
.rdots{left:558px;top:2813px;display:flex;gap:10px}
.rdots i{display:block;width:13px;height:13px;border-radius:50%;background:#c9c9c9}
.rdots i.on{background:var(--teal)}

/* footer */
.footer{left:0;top:2879px;width:1200px;height:320px;background:var(--footer)}
.fcol{top:2926px;color:var(--white)}
.fcol h4{font-size:16px;font-weight:500;margin-bottom:19px}
.fcol li{list-style:none;display:flex;align-items:flex-start;gap:14px;font-size:14px;line-height:26px;margin-bottom:6.5px}
.fcol li svg{flex:none;margin-top:6px}
.signup-text{font-size:14px;line-height:22px;width:290px}
.signup{margin-top:26px;width:292px;height:44px;border-radius:22px;background:var(--white);display:flex;overflow:hidden}
.signup span{flex:1;padding-left:17px;display:flex;align-items:center;font-size:13px;color:var(--muted)}
.signup b{width:48px;background:var(--teal);display:flex;align-items:center;justify-content:center}
.frule{left:111px;top:3145px;width:977px;height:1px;background:#777}
.copy{left:0;width:1200px;top:3163px;text-align:center;font-size:11px;color:var(--white)}
.social-foot{left:1004px;top:3153px;display:flex;gap:9px}
</style>
</head>
<body>

<!-- header -->
<div class="abs call">
  <div class="call-icon"><svg width="16" height="16" viewBox="0 0 24 24"><path d="M6.6 10.8a15 15 0 0 0 6.6 6.6l2.2-2.2c.3-.3.7-.4 1-.2 1.1.4 2.3.6 3.6.6.6 0 1 .4 1 1V20c0 .6-.4 1-1 1A17 17 0 0 1 3 4c0-.6.4-1 1-1h3.5c.6 0 1 .4 1 1 0 1.3.2 2.5.6 3.6.1.3 0 .7-.2 1z" fill="#8fa3ad"/></svg></div>
  <div><small>CALL US:</small><strong>855-310-4478</strong></div>
</div>
<div class="abs header-rule" style="left:265px;width:257px"></div>
<div class="abs header-rule" style="left:678px;width:257px"></div>
<div class="abs brand">
  <div class="brand-dot"></div>
  <div class="brand-name">Marwick Jewelers</div>
</div>
<div class="abs social-top">
  <div class="social-btn"><svg width="14" height="14" viewBox="0 0 14 14"><circle cx="3" cy="7" r="2" fill="#fff"/><circle cx="11" cy="3" r="2" fill="#fff"/><circle cx="11" cy="11" r="2" fill="#fff"/><path d="M3 7 11 3M3 7l8 4" stroke="#fff" stroke-width="1.2"/></svg></div>
  <div class="social-btn light"><svg width="14" height="14" viewBox="0 0 14 14"><path d="M5.5 8.5 8.5 5.5M6 3.5l1-1a2.5 2.5 0 0 1 3.5 3.5l-1 1M8 10.5l-1 1A2.5 2.5 0 0 1 3.5 8l1-1" fill="none" stroke="#5fa2b8" stroke-width="1.4" stroke-linecap="round"/></svg></div>
</div>

<nav class="abs nav">
  <span class="active">Home</span><span>Company</span><span>Custom Jewelery Services &#8964;</span><span>Jewelery Repair Services</span><span>Resources</span><span>Showcase</span><span>Gallery</span><span>Engraving &amp; Trophies</span><span>Gift Ideast</span>
</nav>

<!-- hero -->
<div class="abs hero" role="img" aria-label="Woman by the sea with hands to her face, wearing stacked rings and bracelets"></div>
<h1 class="abs hero-title script">Say It <span class="accent">with a Stone</span></h1>
<p class="abs hero-copy">From “will you?” to “I do” and every momentous occasion<br>in between, Marwick Jewelers offers</p>
<div class="abs btn hero-btn">CONTACT US</div>
<div class="abs dots-pill"><i></i><i class="on"></i><i></i><i></i></div>

<!-- categories -->
<h2 class="abs section-title script" style="left:110px;top:806px">Product <span class="accent">Categories</span></h2>
<div class="abs arrow light" style="left:1005px;top:823px"><svg width="10" height="10" viewBox="0 0 10 10"><path d="M6.5 1 2.5 5l4 4" fill="none" stroke="#333" stroke-width="1.6"/></svg></div>
<div class="abs arrow dark" style="left:1050px;top:823px"><svg width="10" height="10" viewBox="0 0 10 10"><path d="M3.5 1 7.5 5l-4 4" fill="none" stroke="#fff" stroke-width="1.6"/></svg></div>

<div class="abs cat" style="left:112px;background:#f1e4e0" role="img" aria-label="Rose gold ring with interlocking pavé circles"><div class="abs cat-label">RINGS</div></div>
<div class="abs cat" style="left:446px;background:#d9e7e5" role="img" aria-label="Gold beaded bangle"><div class="abs cat-label">PENDANTS</div></div>
<div class="abs cat" style="left:780px;background:#f1e8e0" role="img" aria-label="Rose gold wrap ring with diamond flower"><div class="abs cat-label">EARRINGS</div></div>

<!-- about -->
<div class="abs about-band"></div>
<div class="abs about-photo" role="img" aria-label="Woman sitting on seaside rocks wearing bracelets and anklets"></div>
<h2 class="abs about-title script">About Us</h2>
<div class="abs about-copy">
  <p>From “will you?” to “I do” and every momentous occasion in between, Marwick Jewelers offers a radiant array of elegant stones and settings to take her breath away.&nbsp; Our family-owned store here in Lindholm, MN upholds this promise we made more than 40 years ago: to provide professional expertise that helps you give a gift with a personal touch.</p>
  <p>Browse our online collection of fine jewelry and then visit us in person. Together we’ll find a piece that speaks from the heart.</p>
</div>
<div class="abs btn about-btn">READ MORE</div>

<!-- featured -->
<h2 class="abs section-title script" style="left:0;width:1200px;text-align:center;top:1882px">Featured <span class="accent">Products</span></h2>
<div class="abs arrow light" style="left:38px;top:2097px"><svg width="10" height="10" viewBox="0 0 10 10"><path d="M6.5 1 2.5 5l4 4" fill="none" stroke="#333" stroke-width="1.6"/></svg></div>
<div class="abs arrow dark" style="left:1123px;top:2097px"><svg width="10" height="10" viewBox="0 0 10 10"><path d="M3.5 1 7.5 5l-4 4" fill="none" stroke="#fff" stroke-width="1.6"/></svg></div>

<div class="abs prod" style="left:112px"><div class="prod-img"><div role="img" aria-label="Silver ring with pink cushion stone" style="background:radial-gradient(circle,#e3c6d6,#f7f2f5 70%)"></div></div><h3>PRODUCT</h3><p>At vero eos et accusamus et iusto<br>odio dignissimosea.</p></div>
<div class="abs prod" style="left:360px"><div class="prod-img"><div role="img" aria-label="Silver link bracelet watch with dark face" style="background:radial-gradient(circle,#c9cbd0,#f5f5f6 70%)"></div></div><h3>PRODUCT</h3><p>At vero eos et accusamus et iusto<br>odio dignissimosea.</p></div>
<div class="abs prod" style="left:609px"><div class="prod-img"><div role="img" aria-label="Gold multi-band ring with diamond squares" style="background:radial-gradient(circle,#e6cfaa,#faf6ef 70%)"></div></div><h3>PRODUCT</h3><p>At vero eos et accusamus et iusto<br>odio dignissimosea.</p></div>
<div class="abs prod" style="left:857px"><div class="prod-img"><div role="img" aria-label="Rose gold band with blue solitaire" style="background:radial-gradient(circle,#ecd7d4,#fbf7f6 70%)"></div></div><h3>PRODUCT</h3><p>At vero eos et accusamus et iusto<br>odio dignissimosea.</p></div>

<!-- testimonials -->
<div class="abs reviews"></div>
<h2 class="abs section-title script" style="left:0;width:1200px;text-align:center;top:2464px">What Our <span class="accent">Customers Say</span></h2>

<div class="abs review" style="left:200px">
  <svg width="28" height="22" viewBox="0 0 28 22"><path d="M0 22V12C0 5 4 1 11 0v4C7 5 5 8 5 11h6v11zM16 22V12c0-7 4-11 11-12v4c-4 1-6 4-6 7h6v11z" fill="#5fa2b8"/></svg>
  <p>Sed ut perspiciatis unde omnis iste natus error sit voluptatem accusantium doloremque laudantium, totam rem aperiam eaque ipsa quaea.</p>
  <div class="who"><div class="avatar" role="img" aria-label="Customer portrait"></div><div><strong>Nora Hale</strong><small>New York, United States</small></div></div>
</div>
<div class="abs review" style="left:615px">
  <svg width="28" height="22" viewBox="0 0 28 22"><path d="M0 22V12C0 5 4 1 11 0v4C7 5 5 8 5 11h6v11zM16 22V12c0-7 4-11 11-12v4c-4 1-6 4-6 7h6v11z" fill="#5fa2b8"/></svg>
  <p>Sed ut perspiciatis unde omnis iste natus error sit voluptatem accusantium doloremque laudantium, totam rem aperiam eaque ipsa quaea.</p>
  <div class="who"><div class="avatar" role="img" aria-label="Customer portrait"></div><div><strong>Nora Hale</strong><small>New York, United States</small></div></div>
</div>
<div class="abs rdots"><i></i><i class="on"></i><i></i><i></i></div>

<!-- footer -->
<footer class="abs footer"></footer>
<div class="abs fcol" style="left:111px">
  <h4>QUICK LINKS</h4>
  <ul>
    <li><svg width="13" height="13" viewBox="0 0 14 14"><circle cx="7" cy="7" r="7" fill="#5fa2b8"/><path d="M4 7h6M7.5 4.5 10 7 7.5 9.5" fill="none" stroke="#58585a" stroke-width="1.6"/></svg>Company</li>
    <li><svg width="13" height="13" viewBox="0 0 14 14"><circle cx="7" cy="7" r="7" fill="#5fa2b8"/><path d="M4 7h6M7.5 4.5 10 7 7.5 9.5" fill="none" stroke="#58585a" stroke-width="1.6"/></svg>Custom Jewelery Services</li>
    <li><svg width="13" height="13" viewBox="0 0 14 14"><circle cx="7" cy="7" r="7" fill="#5fa2b8"/><path d="M4 7h6M7.5 4.5 10 7 7.5 9.5" fill="none" stroke="#58585a" stroke-width="1.6"/></svg>Jewelery Repair Services</li>
    <li><svg width="13" height="13" viewBox="0 0 14 14"><circle cx="7" cy="7" r="7" fill="#5fa2b8"/><path d="M4 7h6M7.5 4.5 10 7 7.5 9.5" fill="none" stroke="#58585a" stroke-width="1.6"/></svg>Resources</li>
    <li><svg width="13" height="13" viewBox="0 0 14 14"><circle cx="7" cy="7" r="7" fill="#5fa2b8"/><path d="M4 7h6M7.5 4.5 10 7 7.5 9.5" fill="none" stroke="#58585a" stroke-width="1.6"/></svg>More</li>
  </ul>
</div>
<div class="abs fcol" style="left:368px">
  <h4>MARWICK JEWELERS</h4>
  <ul>
    <li><svg width="13" height="13" viewBox="0 0 14 14"><path d="M7 1a4 4 0 0 0-4 4c0 3 4 8 4 8s4-5 4-8a4 4 0 0 0-4-4zm0 5.5A1.5 1.5 0 1 1 7 3.5a1.5 1.5 0 0 1 0 3z" fill="#5fa2b8"/></svg>48 Alder Ave N,<br>Lindholm, MN</li>
    <li><svg width="13" height="13" viewBox="0 0 14 14"><rect x="4" y="1" width="6" height="12" rx="1.2" fill="none" stroke="#5fa2b8" stroke-width="1.4"/></svg>612-555-0187</li>
    <li><svg width="13" height="13" viewBox="0 0 24 24"><path d="M6.6 10.8a15 15 0 0 0 6.6 6.6l2.2-2.2c.3-.3.7-.4 1-.2 1.1.4 2.3.6 3.6.6.6 0 1 .4 1 1V20c0 .6-.4 1-1 1A17 17 0 0 1 3 4c0-.6.4-1 1-1h3.5c.6 0 1 .4 1 1 0 1.3.2 2.5.6 3.6.1.3 0 .7-.2 1z" fill="#5fa2b8"/></svg>855-310-4478</li>
  </ul>
</div>
<div class="abs fcol" style="left:583px">
  <h4>STORE HOURS</h4>
  <ul>
    <li><svg width="13" height="13" viewBox="0 0 14 14"><circle cx="7" cy="7" r="6" fill="none" stroke="#5fa2b8" stroke-width="1.4"/><path d="M7 3.5V7l2.5 1.5" fill="none" stroke="#5fa2b8" stroke-width="1.4"/></svg>Mon - Sat:<br>10.00 am - 06.00 pm</li>
  </ul>
</div>
<div class="abs fcol" style="left:796px">
  <h4>SIGN UP NOW</h4>
  <p class="signup-text">Sed ut perspiciatis unde omnis iste natus error sit volupta.</p>
  <div class="signup"><span>Email Address</span><b><svg width="16" height="16" viewBox="0 0 16 16"><path d="M15 1 1 7l5 2 2 5zM6 9l9-8" fill="none" stroke="#fff" stroke-width="1.3" stroke-linejoin="round"/></svg></b></div>
</div>
<div class="abs frule"></div>
<div class="abs copy">© 2022 Marwick &nbsp;|&nbsp; All Rights Reserved</div>
<div class="abs social-foot">
  <div class="social-btn"><svg width="14" height="14" viewBox="0 0 14 14"><circle cx="3" cy="7" r="2" fill="#fff"/><circle cx="11" cy="3" r="2" fill="#fff"/><circle cx="11" cy="11" r="2" fill="#fff"/><path d="M3 7 11 3M3 7l8 4" stroke="#fff" stroke-width="1.2"/></svg></div>
  <div class="social-btn light"><svg width="14" height="14" viewBox="0 0 14 14"><path d="M5.5 8.5 8.5 5.5M6 3.5l1-1a2.5 2.5 0 0 1 3.5 3.5l-1 1M8 10.5l-1 1A2.5 2.5 0 0 1 3.5 8l1-1" fill="none" stroke="#5fa2b8" stroke-width="1.4" stroke-linecap="round"/></svg></div>
</div>

</body>
</html>
```